Sticker for Scrap Metal Bin that is placed at customers premises

During the course of our operation, Scrap Metal Bin are place at our customer site for them to dispose scrap metal into the Bin.

Would like to have a sticker for us to paste on the bin.

All scrap bin will be blue color. Attached sample of current sticker on a scrap bin.

Would like one that is clean, simple and eye catching also that the font is much visible unlike the current one that is cramp and small.

Target Market(s)

Businesses

Font styles to use
Serif

Requirements
Must have
• 1) Company Name and Logo
• 2) Contact Details : 9413 5207 / 6582 3046
• 3) Website: www.korvamelt.com

```html
<!DOCTYPE html>
<html lang="en">
<head>
<meta charset="utf-8">
<title>Korva Melt Recycling – Scrap Metal Bin Sticker</title>
<link rel="stylesheet" href="https://fonts.googleapis.com/css2?family=Krona+One&family=Oswald:wght@500&display=swap">
<style>
  :root {
    --bin-blue: #3d7aa0;
    --sticker-white: #ffffff;
    --signal-yellow: #fcd406;
    --ink: #1d1d1b;
    --gold: #c9962e;
    --shadow: rgba(0, 0, 0, 0.55);
  }
  html, body {
    margin: 0;
    padding: 0;
    width: 1200px;
    height: 800px;
    overflow: hidden;
    background: var(--bin-blue);
  }
  .canvas {
    position: relative;
    width: 1200px;
    height: 800px;
    background: var(--bin-blue);
  }
  .sticker {
    position: absolute;
    left: 168px;
    top: 111px;
    width: 864px;
    height: 575px;
    background: var(--sticker-white);
    box-shadow: 10px 12px 22px var(--shadow);
  }
  .brand {
    position: absolute;
    left: 0;
    top: 0;
    width: 100%;
    height: 269px;
  }
  .brand-square {
    position: absolute;
    left: 377px;
    top: 30px;
    width: 112px;
    height: 108px;
    border: 3px solid var(--gold);
  }
  .brand-name {
    position: absolute;
    left: 0;
    width: 100%;
    text-align: center;
    font-family: "Krona One", sans-serif;
    color: var(--gold);
    margin: 0;
    line-height: 1;
  }
  .brand-name .name-main {
    position: absolute;
    left: 0;
    width: 100%;
    top: 180px;
    font-size: 40px;
    letter-spacing: 1px;
  }
  .brand-name .name-sub {
    position: absolute;
    left: 0;
    width: 100%;
    top: 226px;
    font-size: 22px;
    letter-spacing: 2px;
    padding-left: 200px;
    box-sizing: border-box;
  }
  .hazard-band {
    position: absolute;
    left: 0;
    top: 269px;
    width: 100%;
    height: 222px;
    background: var(--signal-yellow);
  }
  .recycle-art {
    position: absolute;
    left: 42px;
    top: 16px;
    width: 184px;
    height: 184px;
    border-radius: 50%;
    background: radial-gradient(circle, #ffffff 0 54%, var(--ink) 55% 100%);
  }
  .band-divider {
    position: absolute;
    left: 243px;
    top: 18px;
    width: 6px;
    height: 198px;
    background: var(--ink);
    border-radius: 3px;
  }
  .band-title {
    position: absolute;
    left: 300px;
    top: 22px;
    margin: 0;
    font-family: "Krona One", sans-serif;
    font-size: 86px;
    line-height: 92px;
    color: var(--ink);
    letter-spacing: 1px;
    font-weight: 400;
  }
  .contact-bar {
    position: absolute;
    left: 0;
    top: 491px;
    width: 100%;
    height: 84px;
  }
  .phone-icon {
    position: absolute;
    left: 42px;
    top: 17px;
    width: 48px;
    height: 48px;
  }
  .contact-text {
    position: absolute;
    top: 18px;
    margin: 0;
    font-family: "Oswald", sans-serif;
    font-weight: 500;
    font-size: 30px;
    line-height: 44px;
    color: var(--ink);
    text-shadow: 2px 2px 0 #9a9a9a;
  }
  .contact-phone { left: 100px; }
  .contact-web { right: 46px; }
</style>
</head>
<body>
<main class="canvas">
  <section class="sticker">
    <header class="brand">
      <div class="brand-square"></div>
      <h1 class="brand-name">
        <span class="name-main">KORVA MELT</span>
        <span class="name-sub">RECYCLING</span>
      </h1>
    </header>

    <div class="hazard-band">
      <div class="recycle-art" role="img" aria-label="Recycling arrows circling a metal bolt illustration"></div>
      <div class="band-divider"></div>
      <h2 class="band-title">SCRAP<br>METAL</h2>
    </div>

    <footer class="contact-bar">
      <svg class="phone-icon" viewBox="0 0 48 48" aria-hidden="true">
        <circle cx="24" cy="24" r="24" fill="var(--signal-yellow)"/>
        <path d="M17 13c1-1 2.5-1 3.3 0l2.6 3.6c.7 1 .5 2.2-.3 3l-1.6 1.5c1 2.6 3.2 4.9 5.9 6l1.5-1.6c.8-.8 2-1 3-.3l3.6 2.6c1 .8 1 2.3 0 3.3l-1.7 1.8c-1.6 1.6-4.2 1.7-6.3.4-5.1-3.1-9.1-7.1-12.2-12.2-1.3-2.1-1.2-4.7.4-6.3z" fill="var(--ink)"/>
      </svg>
      <p class="contact-text contact-phone">:9413 5207 / 6582 3046</p>
      <p class="contact-text contact-web">www.korvamelt.com</p>
    </footer>
  </section>
</main>
</body>
</html>
```